VelkaVision.com

Complete Website Design (Godaddy) and company Branding / Logo Design. The products will sell are only done in-person and are installed. So this site does not need to be an e-commerce site. We will only be giving out information and collecting customer inquires. Website will only need to be about 3 to 5 pages.

```html
<!DOCTYPE html>
<html lang="en">
<head>
<meta charset="utf-8">
<title>VelkaVision – Home</title>
<link rel="stylesheet" href="https://fonts.googleapis.com/css2?family=Exo+2:wght@400;500;700;800&family=Roboto:wght@400;500&display=swap">
<style>
:root{
  --blue-deep:#062a5e;
  --blue:#0b4a9e;
  --blue-mid:#1a5fb4;
  --navy:#031a3c;
  --orange:#de8a12;
  --white:#ffffff;
  --grey-line:#b9bcc4;
  --ghost:#e9eaed;
  --text-muted:#6a6f7a;
}
*{margin:0;padding:0;box-sizing:border-box}
html,body{width:855px;height:1200px;overflow:hidden;background:#fff}
body{font-family:"Exo 2",sans-serif;position:relative}
.page{position:relative;width:855px;height:1200px;overflow:hidden}
.abs{position:absolute}

/* hero */
.hero-media{left:0;top:0;width:855px;height:470px;
  background:radial-gradient(ellipse at 50% 10%,#5b8fd0 0%,#2a62ad 30%,#0d3a7a 60%,#072a5c 100%)}
.hero-screen{left:245px;top:125px;width:340px;height:185px;background:rgba(3,25,60,.75);border:2px solid rgba(120,150,200,.35)}
.logo{left:103px;top:32px;font-weight:800;font-size:29px;color:var(--white);letter-spacing:.2px}
.call{left:550px;top:14px;display:flex;align-items:center;gap:6px;color:var(--white);font-weight:700;font-size:13px}
.call .dot{width:18px;height:18px;border-radius:50%;background:var(--orange);display:flex;align-items:center;justify-content:center}
.nav{left:420px;top:44px;display:flex;gap:22px;font-weight:700;font-size:11px;color:var(--white)}
.nav .active{border-bottom:2px solid var(--orange);padding-bottom:2px}
.search{left:731px;top:41px;width:21px;height:21px;border-radius:50%;background:var(--orange);display:flex;align-items:center;justify-content:center}
.hero-title{left:0;width:855px;top:160px;text-align:center;font-weight:800;font-size:40px;color:var(--white);letter-spacing:1px}
.hero-sub{left:0;width:855px;top:215px;text-align:center;font-size:12px;color:var(--white)}
.btn{display:flex;align-items:center;justify-content:center;background:var(--orange);color:var(--white);font-weight:700;font-size:10px;border-radius:20px;font-family:"Exo 2",sans-serif}
.btn-hero{left:375px;top:249px;width:105px;height:39px}
.dots{left:413px;top:337px;display:flex;gap:6px}
.dots span{width:5px;height:5px;border-radius:50%;background:var(--white)}
.dots .on{background:var(--blue-mid)}

/* welcome */
.welcome-bg{left:0;top:380px;width:855px;height:310px}
.ghost-about{left:0;top:570px;font-weight:800;font-size:52px;color:rgba(255,255,255,.07)}
.welcome-title{left:105px;top:465px;font-weight:800;font-size:40px;color:var(--white)}
.welcome-text{left:377px;top:470px;width:373px;font-size:10px;line-height:17.1px;color:var(--white);text-align:justify}
.btn-more{left:377px;top:604px;width:106px;height:39px}

/* contact */
.contact-media{left:0;top:690px;width:480px;height:370px;
  background:linear-gradient(100deg,#e2e6ee 0%,#edf0f5 45%,#ffffff 100%)}
.contact-screen{left:140px;top:790px;width:265px;height:148px;background:linear-gradient(180deg,#cfd9ea 0%,#eef1f6 60%,#f6f7f9 100%)}
.contact-title{left:110px;top:728px;font-weight:800;font-size:40px;line-height:51px;color:var(--blue)}
.ghost-contact{left:574px;top:918px;font-weight:800;font-size:54px;color:var(--ghost)}
.field{border:1px solid var(--grey-line);background:#fff;font-size:8.5px;color:var(--text-muted);padding:0 14px;display:flex;align-items:center}
.field.msg{align-items:flex-start;padding-top:12px}
.btn-submit{left:425px;top:894px;width:106px;height:39px}

/* footer */
.footer-bg{left:0;top:985px;width:855px;height:215px}
.info{top:1062px;display:flex;align-items:center;gap:12px;color:var(--white);font-family:"Roboto",sans-serif}
.info .ic{width:43px;height:43px;border-radius:50%;border:1.5px solid var(--white);display:flex;align-items:center;justify-content:center}
.info .ic.fill{background:var(--orange);border-color:var(--orange)}
.info h4{font-weight:500;font-size:9.5px;margin-bottom:6px}
.info p{font-size:8.5px;line-height:17px}
.divider{top:1070px;width:1px;height:27px;background:rgba(255,255,255,.25)}
.rule{left:103px;top:1135px;width:649px;height:1px;background:rgba(255,255,255,.15)}
.copy{left:125px;top:1164px;font-family:"Roboto",sans-serif;font-size:8.5px;color:var(--white)}
.social{left:563px;top:1157px;display:flex;gap:11px}
.social span{width:25px;height:25px;border-radius:50%;background:var(--white)}
</style>
</head>
<body>
<div class="page">

  <!-- hero -->
  <div class="abs hero-media" role="img" aria-label="Wall of television screens showing landscapes and people receding into a bright blue room"></div>
  <div class="abs hero-screen"></div>

  <div class="abs logo">VelkaVision</div>
  <div class="abs call">
    <span class="dot"><svg width="10" height="10" viewBox="0 0 24 24"><path fill="#fff" d="M6.6 10.8a15 15 0 0 0 6.6 6.6l2.2-2.2a1 1 0 0 1 1-.25 11.4 11.4 0 0 0 3.6.57 1 1 0 0 1 1 1V20a1 1 0 0 1-1 1A17 17 0 0 1 3 4a1 1 0 0 1 1-1h3.5a1 1 0 0 1 1 1c0 1.25.2 2.45.57 3.57a1 1 0 0 1-.25 1z"/></svg></span>
    Call : +1 555 014 2290
  </div>
  <nav class="abs nav">
    <span class="active">Home</span><span>About Us</span><span>Services</span><span>News</span><span>Contact Us</span>
  </nav>
  <div class="abs search"><svg width="11" height="11" viewBox="0 0 24 24"><circle cx="10" cy="10" r="6" fill="none" stroke="#fff" stroke-width="3"/><path d="M15 15l6 6" stroke="#fff" stroke-width="3" stroke-linecap="round"/></svg></div>

  <h1 class="abs hero-title">VELKA VISION</h1>
  <p class="abs hero-sub">Sed ut perspiciatis unde omnis iste natus</p>
  <div class="abs btn btn-hero">GET STARTED</div>
  <div class="abs dots"><span class="on"></span><span></span><span></span></div>

  <!-- welcome -->
  <svg class="abs welcome-bg" viewBox="0 0 855 310" preserveAspectRatio="none" role="img" aria-label="Blue background with faint wall of screens">
    <defs>
      <linearGradient id="wg" x1="0" y1="0" x2="0" y2="1">
        <stop offset="0" stop-color="#0c4697"/><stop offset="1" stop-color="#0a4fa8"/>
      </linearGradient>
    </defs>
    <path d="M0 75 Q427 -10 855 75 V310 H0Z" fill="url(#wg)"/>
    <path d="M0 75 Q427 -10 855 75" fill="none" stroke="#fff" stroke-width="3"/>
  </svg>
  <div class="abs ghost-about">ABOUT</div>
  <h2 class="abs welcome-title">WELCOME</h2>
  <p class="abs welcome-text">Sed ut perspiciatis unde omnis iste natus error sit voluptatem accusantium doloremque laudantium, totam rem aperiam, eaque ipsa quae ab illo inventore veritatis et quasi architecto beatae vitae dicta sunt explicabo. Nemo enim ipsam voluptatem quia voluptas sit aspernatur aut odit aut fugit, sed quia consequuntur magni dolores eos qui ratione voluptatem sequi nesciunt. Neque porro quisquam est, qui dolorem ipsum quia dolor sit amet, consectetur, adipisci velit, sed quia non numquaut labore et dolore magnam aliquam quaerat voluptatem</p>
  <div class="abs btn btn-more">READ MORE</div>

  <!-- contact -->
  <div class="abs contact-media" role="img" aria-label="Bright living room with a wall-mounted television, armchair and plant"></div>
  <div class="abs contact-screen"></div>
  <div class="abs ghost-contact">CONTACT</div>
  <h2 class="abs contact-title">QUICK<br>CONTACT</h2>
  <div class="abs field" style="left:424px;top:738px;width:156px;height:35px">Enter Name</div>
  <div class="abs field" style="left:589px;top:738px;width:156px;height:35px">Enter Email</div>
  <div class="abs field" style="left:424px;top:782px;width:156px;height:35px">Phone</div>
  <div class="abs field" style="left:589px;top:782px;width:156px;height:35px">Address</div>
  <div class="abs field msg" style="left:424px;top:825px;width:321px;height:57px">Message</div>
  <div class="abs btn btn-submit">SUBMIT</div>

  <!-- footer -->
  <svg class="abs footer-bg" viewBox="0 0 855 215" preserveAspectRatio="none">
    <path d="M0 75 Q427 -10 855 75 V215 H0Z" fill="var(--navy)"/>
    <path d="M0 75 Q427 -10 855 75" fill="none" stroke="var(--orange)" stroke-width="3"/>
  </svg>

  <div class="abs info" style="left:134px">
    <span class="ic"><svg width="18" height="18" viewBox="0 0 24 24"><path fill="#fff" d="M6.6 10.8a15 15 0 0 0 6.6 6.6l2.2-2.2a1 1 0 0 1 1-.25 11.4 11.4 0 0 0 3.6.57 1 1 0 0 1 1 1V20a1 1 0 0 1-1 1A17 17 0 0 1 3 4a1 1 0 0 1 1-1h3.5a1 1 0 0 1 1 1c0 1.25.2 2.45.57 3.57a1 1 0 0 1-.25 1z"/></svg></span>
    <div><h4>ANY QUESTION AT</h4><p>+1 555 014 2290</p></div>
  </div>
  <div class="abs divider" style="left:302px"></div>
  <div class="abs info" style="left:329px">
    <span class="ic fill"><svg width="20" height="16" viewBox="0 0 24 18"><rect x="1.5" y="1.5" width="21" height="15" rx="2" fill="none" stroke="#fff" stroke-width="2"/><path d="M2 3l10 7 10-7" fill="none" stroke="#fff" stroke-width="2"/></svg></span>
    <div><h4>SEND YOUR MAIL AT</h4><p>info@velkavision.com</p></div>
  </div>
  <div class="abs divider" style="left:508px"></div>
  <div class="abs info" style="left:536px">
    <span class="ic"><svg width="18" height="18" viewBox="0 0 24 24"><path fill="#fff" d="M12 3L2 12h3v8h5v-5h4v5h5v-8h3z"/></svg></span>
    <div><p>123,Nemo enim ipsam voluptatem<br>quia voluptas sit</p></div>
  </div>

  <div class="abs rule"></div>
  <div class="abs copy">© 2024 velkavision. All rights reserved.Privacy &nbsp;|&nbsp; Terms of Use</div>
  <div class="abs social" aria-label="Social media links">
    <span></span><span></span><span></span><span></span><span></span>
  </div>

</div>
</body>
</html>
```